Rollers & Glides.com

Vertical Business Card with focus on branding with our icon. Information on card will be logo, persons name, position, phone number, email address and website. Use the the name Marcus Pellow, position President, phone number 480.915.2267, email Marcus@rollersandglides-demo.com, website www.rollersandglides-demo.com.

```html
<!DOCTYPE html>
<html lang="en">
<head>
<meta charset="utf-8">
<title>Rollers &amp; Glides.com – Business Card</title>
<link rel="stylesheet" href="https://fonts.googleapis.com/css2?family=Arimo:wght@400;700&family=Roboto+Condensed:wght@400&display=swap">
<style>
  :root {
    --backdrop: #0e0e0f;
    --card: #27282a;
    --card-edge: #2f62c0;
    --brand-blue: #3564c4;
    --text-light: #e6e6e8;
    --divider: #3a3b3e;
    --mark-grey: #4a4b4e;
  }
  * { margin: 0; padding: 0; box-sizing: border-box; }
  html, body {
    width: 1200px; height: 820px; overflow: hidden;
    background: var(--backdrop);
  }
  .canvas {
    width: 1200px; height: 820px;
    display: flex; align-items: center; justify-content: center; gap: 40px;
  }
  .card {
    position: relative;
    width: 520px; height: 298px;
    background: var(--card);
    border: 2px solid var(--card-edge);
    overflow: hidden;
  }
  .brand-name {
    font-family: "Roboto Condensed", sans-serif;
    font-weight: 400;
    color: var(--brand-blue);
    letter-spacing: 0.08em;
    white-space: nowrap;
  }

  /* front */
  .card-front .brand-lockup {
    position: absolute; top: 58px; left: 0; right: 0;
    display: flex; align-items: center; justify-content: center; gap: 16px;
  }
  .brand-dot {
    width: 30px; height: 30px; border-radius: 50%;
    background: var(--brand-blue);
  }
  .card-front .brand-name { font-size: 27px; }
  .card-front .divider {
    position: absolute; left: 240px; right: 34px; top: 161px;
    height: 1px; background: var(--divider);
  }
  .contact {
    position: absolute; left: 44px; top: 150px;
    font-family: Arimo, sans-serif; color: var(--text-light);
  }
  .person-name {
    font-weight: 700; font-size: 19px; line-height: 22px; color: var(--brand-blue);
    text-transform: uppercase; letter-spacing: 0.01em; white-space: nowrap;
  }
  .person-role { font-size: 15px; margin-top: 2px; }
  .contact-list { list-style: none; margin-top: 22px; font-size: 15px; }
  .contact-list li { display: flex; align-items: center; gap: 9px; margin-bottom: 4px; white-space: nowrap; }
  .contact-list svg { width: 15px; height: 15px; fill: var(--brand-blue); flex: none; }
  .website {
    position: absolute; right: 34px; top: 176px;
    font-family: Arimo, sans-serif; font-size: 14px; color: var(--text-light);
    white-space: nowrap;
  }
  .website .domain { color: var(--brand-blue); }

  /* back */
  .card-back .brand-circle {
    position: absolute; left: 36px; top: 50px;
    width: 160px; height: 160px; border-radius: 50%;
    border: 20px solid var(--mark-grey);
  }
  .card-back .brand-name {
    position: absolute; right: 28px; bottom: 78px; font-size: 27px;
  }
</style>
</head>
<body>
<main class="canvas">
  <section class="card card-front" aria-label="Business card front">
    <div class="brand-lockup">
      <span class="brand-dot"></span>
      <span class="brand-name">Rollers &amp; Glides.com</span>
    </div>
    <div class="divider"></div>
    <div class="contact">
      <p class="person-name">Marcus Pellow</p>
      <p class="person-role">President</p>
      <ul class="contact-list">
        <li>
          <svg viewBox="0 0 24 24" aria-hidden="true"><path d="M6.6 10.8a15.1 15.1 0 0 0 6.6 6.6l2.2-2.2a1 1 0 0 1 1-.25 11.4 11.4 0 0 0 3.6.57 1 1 0 0 1 1 1V20a1 1 0 0 1-1 1A17 17 0 0 1 3 4a1 1 0 0 1 1-1h3.5a1 1 0 0 1 1 1c0 1.25.2 2.450.57 3.57a1 1 0 0 1-.25 1z"/></svg>
          <span>480.915.2267</span>
        </li>
        <li>
          <svg viewBox="0 0 24 24" aria-hidden="true"><path d="M2 5h20v14H2zM3.5 6.5l8.5 6.5 8.5-6.5v-.1H3.5z"/></svg>
          <span>Marcus@rollersandglides-demo.com</span>
        </li>
      </ul>
    </div>
    <p class="website">www.<span class="domain">rollersandglides-demo</span>.com</p>
  </section>

  <section class="card card-back" aria-label="Business card back">
    <div class="brand-circle"></div>
    <span class="brand-name">Rollers &amp; Glides.com</span>
  </section>
</main>
</body>
</html>
```